RWT Fittings Ltd Business Cards

We need a business card with our business logo. We provide window and door installations on high-rises in west coast British Colombia, Canada.

I would like my business information and details on one side of the card, and the other side the company name with logo

Target Market(s)

General Contractors

Industry/Entity Type

Construction

Contact Information for Business Card

one side i want my company name and logo in the dark theme logo that i provided

Requirements
Must have
• Marco Peltieri, 16045518293, RWTFittings@mailbox-demo.com, 1407-5194 Linden Row Burnaby BC, V5H 2K9, Owner & Manager

```html
<!DOCTYPE html>
<html lang="en">
<head>
<meta charset="utf-8">
<title>RWT Fittings Ltd – Business Cards</title>
<link rel="stylesheet" href="https://fonts.googleapis.com/css2?family=Open+Sans:wght@400;700&display=swap">
<style>
  :root {
    --backdrop: #474747;
    --card: #181818;
    --brand-blue: #29a9e1;
    --ink-light: #f2f2f2;
    --edge: #5c5c5c;
  }
  * { box-sizing: border-box; margin: 0; padding: 0; }
  html, body {
    width: 1200px; height: 801px; overflow: hidden;
    background: var(--backdrop);
    font-family: "Open Sans", Arial, sans-serif;
  }
  .canvas { position: relative; width: 1200px; height: 801px; }
  .card {
    position: absolute; top: 246px;
    width: 540px; height: 309px;
    background: var(--card);
    border: 1px solid var(--edge);
    overflow: hidden;
  }
  .card--contact { left: 45px; }
  .card--brand { left: 615px; }

  /* Contact side */
  .brand-mark {
    position: absolute; left: 32px; top: 44px;
    display: flex; align-items: center; gap: 12px;
  }
  .brand-mark__square { width: 26px; height: 26px; background: var(--brand-blue); }
  .brand-mark__name {
    color: var(--brand-blue); font-weight: 700; font-size: 30px;
    letter-spacing: 0.5px; line-height: 1;
  }
  .name-tab {
    position: absolute; left: 0; top: 150px;
    width: 34px; height: 40px; background: var(--brand-blue);
  }
  .person { position: absolute; left: 48px; top: 148px; }
  .person__name {
    color: var(--brand-blue); font-weight: 700; font-size: 22px;
    letter-spacing: 0.5px; line-height: 1.1; text-transform: uppercase;
  }
  .person__role { color: var(--ink-light); font-size: 15px; line-height: 1.3; }
  .divider {
    position: absolute; left: 85px; right: 30px; top: 212px;
    height: 1px; background: var(--brand-blue);
  }
  .contact-list {
    position: absolute; left: 70px; top: 224px;
    list-style: none; color: var(--ink-light); font-size: 12.5px; line-height: 22px;
  }
  .contact-list li { display: flex; align-items: center; gap: 8px; }
  .contact-list svg { width: 12px; height: 12px; flex: none; }
  .address {
    position: absolute; right: 24px; top: 226px;
    color: var(--ink-light); font-size: 13px; line-height: 20px; text-align: right;
  }

  /* Brand side */
  .brand-face {
    position: absolute; inset: 0;
    display: flex; align-items: center; justify-content: center; gap: 20px;
  }
  .brand-face__square { width: 52px; height: 52px; background: var(--brand-blue); }
  .brand-face__name {
    color: var(--brand-blue); font-weight: 700; font-size: 52px;
    letter-spacing: 1px; line-height: 1;
  }
</style>
</head>
<body>
<main class="canvas">
  <section class="card card--contact" aria-label="Business card, contact side">
    <div class="brand-mark">
      <span class="brand-mark__square"></span>
      <span class="brand-mark__name">RWT Fittings Ltd</span>
    </div>

    <span class="name-tab"></span>
    <div class="person">
      <p class="person__name">Marco Peltieri</p>
      <p class="person__role">Owner &amp; Manager</p>
    </div>

    <span class="divider"></span>

    <ul class="contact-list">
      <li>
        <svg viewBox="0 0 24 24" aria-hidden="true"><path fill="#29a9e1" d="M6.6 10.8a15.1 15.1 0 0 0 6.6 6.6l2.2-2.2a1 1 0 0 1 1-.25 11.4 11.4 0 0 0 3.6.57 1 1 0 0 1 1 1V20a1 1 0 0 1-1 1A17 17 0 0 1 3 4a1 1 0 0 1 1-1h3.5a1 1 0 0 1 1 1c0 1.25.2 2.45.57 3.6a1 1 0 0 1-.25 1z"/></svg>
        16045518293
      </li>
      <li>
        <svg viewBox="0 0 24 24" aria-hidden="true"><rect x="2" y="5" width="20" height="14" fill="#29a9e1"/><path d="M2 5l10 8 10-8" fill="none" stroke="#181818" stroke-width="2"/></svg>
        RWTFittings@mailbox-demo.com
      </li>
      <li>
        <svg viewBox="0 0 24 24" aria-hidden="true"><g fill="none" stroke="#29a9e1" stroke-width="2.2"><circle cx="12" cy="12" r="9.5"/><ellipse cx="12" cy="12" rx="4" ry="9.5"/><path d="M2.5 12h19"/></g></svg>
        www.rwtfittings-demo.com
      </li>
    </ul>

    <address class="address" style="font-style: normal;">
      1407-5194 Linden Row<br>Burnaby BC, V5H 2K9
    </address>
  </section>

  <section class="card card--brand" aria-label="Business card, brand side">
    <div class="brand-face">
      <span class="brand-face__square"></span>
      <span class="brand-face__name">RWT Fittings Ltd</span>
    </div>
  </section>
</main>
</body>
</html>
```